Re-style home page - eye-catching and unique design for social commerce website

We need a new concept design for BrinoKet's home page.
We don't want to make huge changes but creating a more professional and eye-catching style.

We need to look very serious like a professional services company and in the same time to look like a social network for e-commerce.

Our logo is very captive and you can use to creating something of harmonious.

This is a re-style and I'm excepted to see unique and fresh design like Glimmora.

Target Market(s)

e-commerce and social

Industry/Entity Type

Social

Number of Pages Required

1 page

Font styles to use
Serif
Sans Serif

Requirements
Must have
• An eye-catching result.
• Search bar with logo and Login How it works and business
• The slogan with login and signup.
• Footer links.
Nice to have
• I would like to open the home page and see only two clear ways:
• -Consumer
• --Search
• --The slogan
• --Login and Signup
• --How it works
• -Business
• --Go to Business area
• Background: City, Shopping.
Should not have
• Scrollbar style!

```html
<!DOCTYPE html>
<html lang="en">
<head>
<meta charset="utf-8">
<title>BrinoKet — Shop directly from your profile</title>
<link rel="stylesheet" href="https://fonts.googleapis.com/css2?family=Montserrat:wght@400;500;600;700&display=swap">
<style>
  :root {
    --navy-deep: #1b1a4e;
    --navy-mid: #2c2a6b;
    --violet: #4b3f86;
    --dusk: #6a5a8e;
    --white: #ffffff;
    --white-soft: rgba(255,255,255,0.85);
    --rule: rgba(255,255,255,0.35);
    --red: #d0302f;
    --text-dark: #3a3a44;
    --icon-grey: #9a9aa4;
  }
  * { box-sizing: border-box; margin: 0; padding: 0; }
  html, body { width: 1200px; height: 675px; overflow: hidden; }
  body { font-family: "Montserrat", Arial, sans-serif; color: var(--white); }

  .home { position: relative; width: 1200px; height: 675px; overflow: hidden; }

  .city-backdrop {
    position: absolute; inset: 0;
    background:
      radial-gradient(ellipse at 25% 35%, rgba(120,100,150,0.55) 0%, rgba(0,0,0,0) 45%),
      radial-gradient(ellipse at 75% 25%, rgba(140,120,160,0.45) 0%, rgba(0,0,0,0) 40%),
      radial-gradient(ellipse at 50% 80%, rgba(110,80,110,0.35) 0%, rgba(0,0,0,0) 50%),
      linear-gradient(180deg, var(--violet) 0%, var(--navy-mid) 55%, var(--navy-deep) 100%);
  }

  .brand {
    position: absolute; left: 0; right: 0; top: 86px;
    display: flex; justify-content: center; align-items: center; gap: 8px;
  }
  .brand-name { font-size: 31px; font-weight: 700; letter-spacing: -0.3px; color: var(--white); }
  .brand-mark { width: 16px; height: 16px; background: #f0a23a; }

  .headline {
    position: absolute; left: 0; right: 0; top: 154px; text-align: center;
    font-size: 25.5px; font-weight: 700; letter-spacing: 0.1px;
  }
  .tagline {
    position: absolute; left: 0; right: 0; top: 191px; text-align: center;
    font-size: 15.5px; font-weight: 500;
  }

  .feed-label {
    position: absolute; left: 0; right: 0; top: 253px; text-align: center;
    font-size: 11px; font-weight: 600;
  }
  .select {
    position: absolute; top: 282px; width: 176px; height: 33px;
    background: var(--white); border-radius: 2px;
    display: flex; align-items: center; padding: 0 12px;
    color: var(--text-dark); font-size: 11.5px; font-weight: 500;
  }
  .select-interest { left: 420px; }
  .select-city { left: 605px; padding-left: 10px; }
  .select .pin { margin-right: 7px; }
  .select .chevron { margin-left: auto; }
  .search-icon { position: absolute; left: 800px; top: 290px; }

  .btn-signup {
    position: absolute; left: 495px; top: 340px; width: 220px; height: 40px;
    background: var(--red); border-radius: 2px;
    display: flex; align-items: center; justify-content: center;
    font-size: 12.5px; font-weight: 500; color: var(--white);
  }
  .divider {
    position: absolute; left: 495px; top: 392px; width: 220px;
    display: flex; align-items: center; gap: 8px;
    font-size: 10px; font-weight: 500;
  }
  .divider::before, .divider::after { content: ""; flex: 1; height: 1px; background: var(--rule); }
  .login-link {
    position: absolute; left: 0; right: 0; top: 415px; text-align: center;
    font-size: 13px; font-weight: 500;
  }

  .btn-business {
    position: absolute; left: 470px; top: 473px; width: 165px; height: 33px;
    border: 1px solid var(--white); border-radius: 3px;
    display: flex; align-items: center; justify-content: center; gap: 6px;
    font-size: 12.5px; font-weight: 500;
  }
  .how-link {
    position: absolute; left: 654px; top: 482px;
    font-size: 11.5px; font-weight: 500;
  }

  .footer-nav {
    position: absolute; left: 0; right: 0; top: 580px;
    display: flex; justify-content: center; gap: 26px;
    font-size: 10.5px; font-weight: 500; list-style: none;
  }
  .copyright {
    position: absolute; left: 0; right: 0; top: 612px; text-align: center;
    font-size: 9px; font-weight: 500; color: var(--white-soft);
  }
</style>
</head>
<body>
<main class="home">
  <div class="city-backdrop" role="img" aria-label="Blurred photo of a busy city shopping street with crowds of shoppers, tinted deep violet"></div>

  <div class="brand">
    <span class="brand-name">BrinoKet</span>
    <span class="brand-mark"></span>
  </div>

  <h1 class="headline">Shop directly from your profile</h1>
  <p class="tagline">Save your time. Live better.</p>

  <p class="feed-label">Setup your feed</p>

  <div class="select select-interest">
    <span>Active life</span>
    <svg class="chevron" width="12" height="8" viewBox="0 0 12 8"><path d="M1 1.5l5 5 5-5" fill="none" stroke="#3a3a44" stroke-width="1.6"/></svg>
  </div>
  <div class="select select-city">
    <svg class="pin" width="9" height="13" viewBox="0 0 9 13"><path d="M4.5 0C2 0 0 2 0 4.5 0 8 4.5 13 4.5 13S9 8 9 4.5C9 2 7 0 4.5 0zm0 6.3a1.8 1.8 0 1 1 0-3.6 1.8 1.8 0 0 1 0 3.6z" fill="#9a9aa4"/></svg>
    <span>London</span>
    <svg class="chevron" width="12" height="8" viewBox="0 0 12 8"><path d="M1 1.5l5 5 5-5" fill="none" stroke="#3a3a44" stroke-width="1.6"/></svg>
  </div>
  <svg class="search-icon" width="17" height="17" viewBox="0 0 17 17"><circle cx="7" cy="7" r="5.5" fill="none" stroke="#ffffff" stroke-width="2"/><path d="M11 11l4.5 4.5" stroke="#ffffff" stroke-width="2.2" stroke-linecap="round"/></svg>

  <a class="btn-signup">Sign Up</a>
  <div class="divider">or</div>
  <a class="login-link">Login</a>

  <a class="btn-business">Go to Business Area
    <svg width="18" height="8" viewBox="0 0 18 8"><path d="M0 4h16M13 1l3 3-3 3" fill="none" stroke="#ffffff" stroke-width="1"/></svg>
  </a>
  <a class="how-link">How it works</a>

  <ul class="footer-nav">
    <li>About Us</li><li>Blog</li><li>Business</li><li>Jobs</li><li>Privacy</li><li>FAQ</li><li>Contacts</li>
  </ul>
  <p class="copyright">© 2015 BrinoKet. All right reserved.</p>
</main>
</body>
</html>
```